Kestrelbrook Student Accomodation needs a business card design

Hi Guys,

We are a Student Accommodation company in Australia. We already have a logo which I will submit.

I will require the design of the business cards from you.

I am after something that looks clean, modern and that people feel interested and actually want to contact us.

We would like to see designs that are innovative.

On the business cards I will require to have:

Employee Name
Position
Phone number
Email
Facebook page

I hope you can help me with this project guys as I have heard really good things from you.

```html
<!DOCTYPE html>
<html lang="en">
<head>
<meta charset="utf-8">
<title>Kestrelbrook Student Accomodation – Business Card</title>
<link href="https://fonts.googleapis.com/css2?family=Open+Sans:wght@400;600;700&display=swap" rel="stylesheet">
<style>
  :root {
    --green: #0a8c45;
    --gold: #e9a825;
    --ink: #3a3a3a;
    --white: #ffffff;
    --backdrop: #e9e6e1;
    --social: #3b5a98;
  }
  * { box-sizing: border-box; margin: 0; padding: 0; }
  html, body { width: 1200px; height: 765px; overflow: hidden; }
  body {
    background: var(--backdrop);
    font-family: "Open Sans", Arial, sans-serif;
    position: relative;
  }
  .card {
    position: absolute;
    width: 600px;
    height: 343px;
    background: var(--white);
    border: 1px solid #c9c9c9;
    overflow: hidden;
  }
  .card--front { left: 60px; top: 40px; }
  .card--back { left: 540px; top: 405px; }

  .card__art { position: absolute; inset: 0; width: 100%; height: 100%; }

  .brand {
    position: absolute;
    display: flex;
    align-items: center;
    gap: 10px;
  }
  .brand__mark { background: var(--gold); flex: none; }
  .brand__name {
    color: var(--green);
    font-weight: 700;
    line-height: 1.05;
    text-transform: uppercase;
  }
  .card--front .brand { left: 92px; top: 62px; }
  .card--front .brand__mark { width: 34px; height: 34px; }
  .card--front .brand__name { font-size: 21px; }

  .card--back .brand { left: 0; right: 0; top: 0; bottom: 0; justify-content: center; }
  .card--back .brand__mark { width: 48px; height: 48px; }
  .card--back .brand__name { font-size: 30px; }

  .contact {
    position: absolute;
    left: 32px;
    top: 186px;
    list-style: none;
    color: var(--ink);
    font-size: 15.5px;
  }
  .contact__item { display: flex; align-items: center; gap: 8px; height: 28px; }
  .contact__icon { width: 13px; height: 13px; flex: none; }
  .contact__square { width: 13px; height: 13px; background: var(--social); flex: none; }

  .person {
    position: absolute;
    right: 8px;
    top: 283px;
    text-align: right;
    color: var(--white);
  }
  .person__name { font-size: 20px; font-weight: 700; line-height: 1.2; }
  .person__role { font-size: 15px; font-weight: 400; }
</style>
</head>
<body>

<section class="card card--front">
  <svg class="card__art" viewBox="0 0 600 343" aria-hidden="true">
    <polygon points="0,0 60,0 0,40" fill="var(--green)"/>
    <polygon points="0,318 600,226 600,343 0,343" fill="var(--green)"/>
    <line x1="0" y1="306" x2="600" y2="214" stroke="var(--gold)" stroke-width="3"/>
  </svg>

  <div class="brand">
    <span class="brand__mark"></span>
    <span class="brand__name">Kestrelbrook<br>Student<br>Accomodation</span>
  </div>

  <ul class="contact">
    <li class="contact__item">
      <svg class="contact__icon" viewBox="0 0 16 16"><path d="M4 1 L6.5 4.5 L5 6.3 C6 8.5 7.5 10 9.7 11 L11.5 9.5 L15 12 L13.5 15 C7 14.5 1.5 9 1 2.5 Z" fill="var(--green)"/></svg>
      <span>123-456-7890</span>
    </li>
    <li class="contact__item">
      <svg class="contact__icon" viewBox="0 0 16 16"><rect x="1" y="3" width="14" height="10" fill="var(--green)"/><path d="M1 3.5 L8 9 L15 3.5" fill="none" stroke="var(--white)" stroke-width="1.3"/></svg>
      <span>info@kestrelbrook.com</span>
    </li>
    <li class="contact__item">
      <span class="contact__square"></span>
      <span>/kestrelbrookstudents</span>
    </li>
  </ul>

  <div class="person">
    <p class="person__name">Employee Name</p>
    <p class="person__role">Position</p>
  </div>
</section>

<section class="card card--back">
  <div class="brand">
    <span class="brand__mark"></span>
    <span class="brand__name">Kestrelbrook<br>Student<br>Accomodation</span>
  </div>
</section>

</body>
</html>
```